Web design required

1-We need a web design for existing company based in New Zealand
2-We build residential house and light commercial
3-We has in-house designer which allow us can provide interior design
4-We modeling project before site construction, which enable both client and construction team to visually analysis whole project,

Target Market(s)

middle class residential house market
Ref: http://www.parvellbuilders.co.nz/

Industry/Entity Type

Construction Company

Number of Pages Required

1 page

Font styles to use
Sans Serif
Other font styles liked:
• Such as : Central Gothic or similar which has more design taste

Colors

Designer to choose colors to be used in the design.

Requirements
Must have
• Front sheet, contact information, sample project

```html
<!DOCTYPE html>
<html lang="en">
<head>
<meta charset="utf-8">
<title>Kestrel Homes – Construction Modelling</title>
<link href="https://fonts.googleapis.com/css2?family=Montserrat:wght@500;600;700&family=Questrial&family=Open+Sans:wght@400;600&display=swap" rel="stylesheet">
<style>
  :root {
    --blue: #1a6fb0;
    --blue-deep: #0d4f86;
    --ink: #1d1d1d;
    --grey-text: #6a6a6a;
    --white: #ffffff;
    --hero-dark: #2b2a2c;
    --hero-warm: #6b5a44;
    --contact-bg: #3a3836;
    --field: #4a4846;
    --field-line: #8a8886;
    --footer: #2e2d2c;
  }
  * { margin: 0; padding: 0; box-sizing: border-box; }
  html, body { width: 1200px; height: 2748px; overflow: hidden; background: var(--white); }
  body { position: relative; font-family: "Open Sans", Arial, sans-serif; color: var(--ink); }
  .abs { position: absolute; white-space: nowrap; }

  /* Hero */
  .hero { position: absolute; left: 0; top: 0; width: 1200px; height: 667px;
    background: linear-gradient(180deg, #3a4150 0%, #4a4640 35%, var(--hero-warm) 60%, var(--hero-dark) 100%); }
  .hero-shade { position: absolute; inset: 0; background: rgba(0,0,0,0.25); }
  .brand { position: absolute; left: 125px; top: 44px; display: flex; align-items: center; gap: 14px; white-space: nowrap; }
  .brand-mark { width: 38px; height: 38px; border: 3px solid var(--white); }
  .brand-name { font-family: "Questrial", sans-serif; color: var(--white); font-size: 26px; letter-spacing: 2px; line-height: 1; }
  .nav a { position: absolute; top: 46px; font-family: "Montserrat", sans-serif; font-weight: 600; font-size: 14px;
    color: var(--white); text-decoration: none; white-space: nowrap; line-height: 38px; }
  .nav a.active { border: 2px solid rgba(255,255,255,0.75); width: 108px; text-align: center; line-height: 36px; height: 40px; }
  .hero-title { position: absolute; top: 298px; left: 0; width: 1200px; text-align: center; white-space: nowrap;
    font-family: "Montserrat", sans-serif; font-weight: 600; font-size: 44px; letter-spacing: 4px; color: var(--white); }
  .hero-sub { position: absolute; top: 358px; left: 0; width: 1200px; text-align: center; white-space: nowrap;
    font-family: "Montserrat", sans-serif; font-weight: 600; font-size: 32px; color: var(--white); }
  .slider-dots { position: absolute; top: 612px; left: 526px; display: flex; gap: 8px; }
  .slider-dots span { width: 30px; height: 3px; background: var(--white); }
  .slider-dots span.on { background: #6aa8d8; }

  /* About */
  .about-title { left: 139px; top: 766px; font-family: "Questrial", sans-serif; font-size: 31px; z-index: 2; }
  .about-text { left: 139px; top: 824px; width: 360px; font-size: 13.5px; line-height: 20px; color: var(--grey-text); white-space: normal; }
  .about-text p + p { margin-top: 20px; }
  .btn-outline { left: 139px; top: 1021px; width: 169px; height: 40px; border: 2px solid var(--blue);
    color: var(--blue); font-family: "Montserrat", sans-serif; font-weight: 600; font-size: 14px;
    display: flex; align-items: center; justify-content: center; letter-spacing: 0.5px; }
  .about-model { left: 551px; top: 667px; width: 649px; height: 494px;
    background: radial-gradient(ellipse at 55% 50%, #d9d6d0 0%, #ecebe8 45%, #f6f6f6 75%); }

  /* Services */
  .services { left: 0; top: 1161px; width: 1200px; height: 515px; }
  .services-title { left: 115px; top: 1283px; font-family: "Questrial", sans-serif; font-size: 29px; color: var(--white); }
  .services-rule { left: 115px; top: 1322px; width: 62px; height: 2px; background: var(--white); }
  .services-text { left: 115px; top: 1344px; width: 370px; font-size: 14.5px; line-height: 22px; color: var(--white); white-space: normal; }
  .services-text p + p { margin-top: 7px; }
  .strip-title { font-family: "Montserrat", sans-serif; font-weight: 700; font-size: 19px; }
  .strip-text { font-size: 12px; line-height: 18px; width: 320px; margin-top: 6px; white-space: normal; }
  .strip-1 { left: 749px; top: 1207px; color: var(--ink); }
  .strip-1 .strip-text { color: #8a8580; }
  .strip-2 { left: 672px; top: 1382px; color: var(--white); }
  .strip-2 .strip-text { color: #9a9a9a; }
  .strip-3 { left: 581px; top: 1554px; color: var(--white); }
  .strip-3 .strip-text { color: #9a9a9a; }

  /* Projects */
  .projects-title { left: 0; top: 1754px; width: 1200px; text-align: center; font-family: "Questrial", sans-serif; font-size: 31px; }
  .hexes { left: 128px; top: 1810px; }
  .hex-label { font-family: "Montserrat", sans-serif; font-weight: 700; font-size: 17px; fill: var(--white); text-anchor: middle; }

  /* Contact */
  .contact { left: 0; top: 2180px; width: 1200px; height: 491px;
    background: linear-gradient(120deg, #4a4744 0%, var(--contact-bg) 45%, #2f2c2a 100%); }
  .contact-title { left: 0; top: 2222px; width: 1200px; text-align: center; font-family: "Questrial", sans-serif; font-size: 31px; color: var(--white); }
  .field { left: 128px; width: 444px; height: 41px; background: var(--field); border: 1px solid var(--field-line);
    color: #c8c6c4; font-size: 14px; padding: 10px 14px; }
  .field-msg { height: 106px; }
  .btn-send { left: 128px; top: 2574px; width: 134px; height: 44px; background: var(--blue); color: var(--white);
    font-family: "Montserrat", sans-serif; font-weight: 700; font-size: 17px; display: flex; align-items: center; justify-content: center; }
  .office-title { left: 632px; top: 2294px; font-family: "Questrial", sans-serif; font-size: 20px; font-weight: 400; color: #e6e4e2; }
  .info-line { left: 632px; display: flex; align-items: center; gap: 10px; font-family: "Questrial", sans-serif; font-size: 16px; color: #ececec; }
  .info-icon { width: 30px; height: 30px; }
  .socials { left: 630px; top: 2484px; display: flex; gap: 9px; }
  .socials span { width: 35px; height: 35px; border: 2px solid #e6e4e2; border-radius: 50%; }

  .footer { left: 0; top: 2671px; width: 1200px; height: 77px; background: var(--footer);
    color: #b8b6b4; font-size: 14px; display: flex; align-items: center; justify-content: center; }
</style>
</head>
<body>

<header class="hero" role="img" aria-label="Photograph of a two-storey brick family home at dusk with lit windows and trees">
  <div class="hero-shade"></div>
</header>
<div class="brand">
  <span class="brand-mark"></span>
  <span class="brand-name">KESTREL HOMES</span>
</div>
<nav class="nav">
  <a class="active" href="#" style="left:502px">HOME</a>
  <a href="#" style="left:632px">ABOUT US</a>
  <a href="#" style="left:751px">SERVICES</a>
  <a href="#" style="left:870px">PROJECTS</a>
  <a href="#" style="left:991px">CONTACT US</a>
</nav>
<h1 class="hero-title">WELCOME TO KESTREL HOMES</h1>
<p class="hero-sub">CONSTRUCTION MODELLING</p>
<div class="slider-dots"><span></span><span></span><span class="on"></span><span></span></div>

<section>
  <div class="abs about-model" role="img" aria-label="3D cut-away model of a furnished single-storey house floor plan"></div>
  <h2 class="abs about-title">ABOUT KESTREL HOMES</h2>
  <div class="abs about-text">
    <p>Kestrel Homes is dedicated to creating and renovating beautiful and unusual buildings.</p>
    <p>Kestrel Homes works with you to take dream houses off the blueprints and into reality. We have the knowledge and expertise to customise homes to suit you – from unusual materials and designs to environmentally sensitive locations.</p>
  </div>
  <div class="abs btn-outline">READ MORE</div>
</section>

<section>
  <svg class="abs services" width="1200" height="515" viewBox="0 0 1200 515">
    <defs>
      <linearGradient id="blueBand" x1="0" y1="0" x2="1" y2="1">
        <stop offset="0" stop-color="#1f78bb"/>
        <stop offset="1" stop-color="#0b4a82"/>
      </linearGradient>
      <linearGradient id="stripLight" x1="0" y1="0" x2="1" y2="0">
        <stop offset="0" stop-color="#d8d4cc"/>
        <stop offset="1" stop-color="#e8e6e2"/>
      </linearGradient>
      <linearGradient id="stripMid" x1="0" y1="0" x2="1" y2="0">
        <stop offset="0" stop-color="#3e3e42"/>
        <stop offset="1" stop-color="#58585c"/>
      </linearGradient>
      <linearGradient id="stripDark" x1="0" y1="0" x2="1" y2="0">
        <stop offset="0" stop-color="#2a2a2e"/>
        <stop offset="1" stop-color="#3a3a3e"/>
      </linearGradient>
    </defs>
    <rect width="1200" height="515" fill="url(#blueBand)" role="img" aria-label="Blue-tinted photograph of a house exterior"/>
    <polygon points="742,0 1200,0 1200,171 660,171" fill="url(#stripLight)" role="img" aria-label="Photograph of architect drawing tools on plans"/>
    <polygon points="660,171 1200,171 1200,343 580,343" fill="url(#stripMid)" role="img" aria-label="Wireframe render of a building model"/>
    <polygon points="522,343 1200,343 1200,515 432,515" fill="url(#stripDark)" role="img" aria-label="Photograph of a project team meeting"/>
  </svg>
  <h2 class="abs services-title">OUR SERVICES</h2>
  <div class="abs services-rule"></div>
  <div class="abs services-text">
    <p>Vivamus porttitor purus nisi eleifend libero a temp us libero lectus feugiat felis Morbi diam mauris viverra in gravida eu mattis in ante Morbi eget arcu Morbi porta</p>
    <p>libero id ullamcorper nonummy nibh ligula pulvinar metus eget consectetuer augue nisi quis l</p>
  </div>
  <div class="abs strip-1">
    <h3 class="strip-title">PRECONSTRUCTION PLANNING</h3>
    <p class="strip-text">Cum sociis natoque penatibus et magnis dis parturient montes nascetur ridiculus mus in iaculis</p>
  </div>
  <div class="abs strip-2">
    <h3 class="strip-title">CONSTRUCTION MODELLING</h3>
    <p class="strip-text">Cum sociis natoque penatibus et magnis dis parturient montes nascetur ridiculus mus in iaculis</p>
  </div>
  <div class="abs strip-3">
    <h3 class="strip-title">FULL PROJECT MANAGEMENT</h3>
    <p class="strip-text">Cum sociis natoque penatibus et magnis dis parturient montes nascetur ridiculus mus in iaculis facilisis</p>
  </div>
</section>

<section>
  <h2 class="abs projects-title">OUR PROJECTS</h2>
  <svg class="abs hexes" width="950" height="284" viewBox="0 0 950 284">
    <defs>
      <linearGradient id="projA" x1="0" y1="0" x2="0" y2="1"><stop offset="0" stop-color="#6d7580"/><stop offset="1" stop-color="#2b2e33"/></linearGradient>
      <linearGradient id="projB" x1="0" y1="0" x2="0" y2="1"><stop offset="0" stop-color="#3c5f8e"/><stop offset="1" stop-color="#a9a59c"/></linearGradient>
      <linearGradient id="projC" x1="0" y1="0" x2="0" y2="1"><stop offset="0" stop-color="#5b8fc4"/><stop offset="1" stop-color="#2e6aa6"/></linearGradient>
      <linearGradient id="projD" x1="0" y1="0" x2="1" y2="1"><stop offset="0" stop-color="#8a5a3a"/><stop offset="0.5" stop-color="#d9d4cc"/><stop offset="1" stop-color="#a06a44"/></linearGradient>
    </defs>
    <g>
      <polygon points="115,4 229,70 229,214 115,280 1,214 1,70" fill="var(--blue)"/>
      <polygon points="115,4 229,70 229,202 115,268 1,202 1,70" fill="url(#projA)" role="img" aria-label="Photograph of a white villa with letterbox"/>
    </g>
    <g transform="translate(238,0)">
      <polygon points="115,4 229,70 229,214 115,280 1,214 1,70" fill="var(--blue)"/>
      <polygon points="115,4 229,70 229,202 115,268 1,202 1,70" fill="url(#projB)" role="img" aria-label="Photograph of a modern two-storey home at twilight"/>
    </g>
    <g transform="translate(476,0)">
      <polygon points="115,4 229,70 229,214 115,280 1,214 1,70" fill="var(--blue-deep)"/>
      <polygon points="115,4 229,70 229,202 115,268 1,202 1,70" fill="url(#projC)" role="img" aria-label="Blue-tinted photograph of a house under construction"/>
      <text class="hex-label" x="115" y="142">ASHCOMBE</text>
      <text class="hex-label" x="115" y="164">PROJECT</text>
    </g>
    <g transform="translate(714,0)">
      <polygon points="115,4 229,70 229,214 115,280 1,214 1,70" fill="var(--blue)"/>
      <polygon points="115,4 229,70 229,202 115,268 1,202 1,70" fill="url(#projD)" role="img" aria-label="Photograph of timber ceiling and interior details"/>
    </g>
  </svg>
</section>

<section>
  <div class="abs contact" role="img" aria-label="Dimmed photograph of a modern kitchen interior"></div>
  <h2 class="abs contact-title">CONTACT US</h2>
  <div class="abs field" style="top:2301px">Name</div>
  <div class="abs field" style="top:2352px">Email</div>
  <div class="abs field" style="top:2403px">Phone</div>
  <div class="abs field field-msg" style="top:2455px">Message</div>
  <div class="abs btn-send">SEND</div>

  <h3 class="abs office-title">Head Office</h3>
  <div class="abs info-line" style="top:2341px">
    <svg class="info-icon" viewBox="0 0 30 30"><circle cx="15" cy="15" r="13.5" fill="none" stroke="#ececec" stroke-width="1.5"/><path d="M15 7.5a5 5 0 0 0-5 5c0 4 5 10 5 10s5-6 5-10a5 5 0 0 0-5-5z" fill="none" stroke="#ececec" stroke-width="1.6"/><circle cx="15" cy="12.5" r="1.8" fill="#ececec"/></svg>
    <span>18 Harbourview Lane, Eastfield Auckland</span>
  </div>
  <div class="abs info-line" style="top:2383px">
    <svg class="info-icon" viewBox="0 0 30 30"><circle cx="15" cy="15" r="13.5" fill="none" stroke="#ececec" stroke-width="1.5"/><path d="M10.5 8.5l3 3-1.6 1.8c.9 2 2.5 3.6 4.5 4.5l1.8-1.6 3 3-2 2c-5-.6-9.9-5.5-10.6-10.6z" fill="none" stroke="#ececec" stroke-width="1.6" stroke-linejoin="round"/></svg>
    <span>info@kestrelhomes.co.nz</span>
  </div>
  <div class="abs info-line" style="top:2425px">
    <svg class="info-icon" viewBox="0 0 30 30"><circle cx="15" cy="15" r="13.5" fill="none" stroke="#ececec" stroke-width="1.5"/><rect x="8.5" y="10" width="13" height="10" rx="1" fill="none" stroke="#ececec" stroke-width="1.6"/><path d="M8.5 10.5l6.5 5 6.5-5" fill="none" stroke="#ececec" stroke-width="1.6"/></svg>
    <span>Tel: 0064 9 555 0142</span>
  </div>
  <div class="abs socials"><span></span><span></span><span></span><span></span></div>
</section>

<footer class="abs footer">© 2017 Company Name &nbsp;All right reserved &nbsp;Term of Use</footer>

</body>
</html>
```